Fenwick Ridge Accounting - New client package

I need a stationary package (presentation folder cover, welcome letter template/design, sample financial report template/design, business card and new logo) for my accounting business. I would like to see designs that use the color blue. Financial icons can be included in the design. The final design should be clean and communicate professionalism and the use of modern; user-friendly technology. Attached postcard files should help with overall design concept.

```html
<!DOCTYPE html>
<html lang="en">
<head>
<meta charset="utf-8">
<title>Fenwick Ridge Accounting – Presentation Folder</title>
<link rel="stylesheet" href="https://fonts.googleapis.com/css2?family=Montserrat:wght@400;500&family=Arimo:wght@400;700&display=swap">
<style>
  :root {
    --navy: #044f8c;
    --navy-deep: #06488a;
    --sky: #1797cc;
    --white: #ffffff;
    --paper-bg: #e4e4e6;
    --brand-text: #0a4f8f;
  }
  * { margin: 0; padding: 0; box-sizing: border-box; }
  html, body { width: 1200px; height: 854px; overflow: hidden; }
  body {
    background: var(--paper-bg);
    font-family: "Arimo", Arial, sans-serif;
    position: relative;
  }
  .folder-spread {
    position: absolute;
    left: 30px; top: 47px;
    width: 1140px; height: 760px;
    display: flex;
    box-shadow: 0 6px 18px rgba(0,0,0,0.18);
  }
  .panel { position: relative; width: 570px; height: 760px; overflow: hidden; background: var(--white); }
  .panel svg.panel-art { position: absolute; inset: 0; }
  .brand {
    position: absolute;
    display: flex; align-items: center; gap: 12px;
    font-family: "Montserrat", sans-serif;
    font-weight: 500;
    text-transform: uppercase;
    letter-spacing: 0.04em;
  }
  .brand-front { top: 62px; left: 118px; color: var(--brand-text); font-size: 25px; line-height: 1.05; }
  .brand-front .brand-square { width: 26px; height: 26px; background: var(--sky); }
  .brand-back { left: 330px; top: 600px; color: var(--white); font-size: 13px; line-height: 1.1; }
  .brand-back .brand-square { width: 14px; height: 14px; background: var(--sky); }
  .front-web {
    position: absolute; right: 46px; bottom: 78px;
    color: var(--white); font-size: 13px; letter-spacing: 0.01em;
  }
  .front-web strong { font-weight: 700; }
  .back-contact-block {
    position: absolute; left: 58px; bottom: 58px;
    display: flex; align-items: flex-start; gap: 40px;
    color: var(--white); font-size: 10px; line-height: 1.5;
  }
  .back-address { white-space: nowrap; }
  .back-contacts { list-style: none; white-space: nowrap; }
  .back-contacts li { display: flex; align-items: center; gap: 7px; }
  .back-contacts svg { width: 9px; height: 9px; fill: none; stroke: var(--sky); stroke-width: 1.4; flex-shrink: 0; }
</style>
</head>
<body>
  <main class="folder-spread">
    <section class="panel panel-back" aria-label="Folder back cover">
      <svg class="panel-art" width="570" height="760" viewBox="0 0 570 760">
        <path d="M0 400 Q300 350 570 225 L570 760 L0 760 Z" fill="var(--navy)"/>
        <path d="M0 385 Q300 335 570 212 L570 225 Q300 350 0 400 Z" fill="var(--sky)"/>
        <path d="M0 400 Q300 350 570 225 L570 230 Q300 355 0 405 Z" fill="var(--white)"/>
      </svg>
      <div class="brand brand-back">
        <span class="brand-square"></span>
        <span>Fenwick Ridge<br>Accounting</span>
      </div>
      <div class="back-contact-block">
        <p class="back-address">Level 12, Harbour House<br>27 Ferry Road<br>Sydney</p>
        <ul class="back-contacts">
          <li><svg viewBox="0 0 10 10"><path d="M2 1 L4 3 L3 4.5 Q4.5 6.5 5.5 7 L7 6 L9 8 L7.5 9.5 Q2 8 0.5 2.5 Z"/></svg>555-014-2287</li>
          <li><svg viewBox="0 0 10 10"><rect x="0.8" y="2" width="8.4" height="6"/><path d="M0.8 2 L5 5.5 L9.2 2"/></svg>hello@fenwickridge.com</li>
          <li><svg viewBox="0 0 10 10"><circle cx="5" cy="5" r="4"/><path d="M1 5 H9 M5 1 Q2.5 5 5 9 M5 1 Q7.5 5 5 9"/></svg>www.fenwickridge.com</li>
        </ul>
      </div>
    </section>

    <section class="panel panel-front" aria-label="Folder front cover">
      <svg class="panel-art" width="570" height="760" viewBox="0 0 570 760">
        <rect x="0" y="318" width="570" height="442" fill="var(--navy-deep)"/>
        <polygon points="0,300 200,300 210,312 0,312" fill="var(--sky)"/>
        <polygon points="206,300 570,290 570,302 216,310" fill="var(--navy-deep)"/>
        <rect x="0" y="312" width="570" height="6" fill="var(--white)"/>
      </svg>
      <div class="brand brand-front">
        <span class="brand-square"></span>
        <span>Fenwick Ridge<br>Accounting</span>
      </div>
      <p class="front-web">www.<strong>fenwickridge</strong>.com</p>
    </section>
  </main>
</body>
</html>
```